Creative, Colorful, Dynamic Infographic for Global Non-Profit

We are a global arts and education non-profit in need of an infographic that illustrates four key skills embedded in our work: Curiosity, Listening, Imagination, Postive Action.
We work primarily with educators, students, and artists who use the power of personal stories to build community and connection and to bridge divides.
Our new brand guidelines, logos, and fonts are here: https://stylevault.example/lumen-circle
I've attached a mock-up of the graphic and the required text. (Note the attached design was created by a staff person, your final design does not need to be the same. The color scheme and text of the final design should match the brand guidelines above.)
The graphic will be used for both web and print media and should include the purple Lumen Circle logo (also attached).
Ideally the final design will delight audiences and spark interest in our work.

```html
<!DOCTYPE html>
<html lang="en">
<head>
<meta charset="utf-8">
<title>Lumen Circle – 4 Key Skills</title>
<link href="https://fonts.googleapis.com/css2?family=Archivo:wght@500;700&family=Montserrat:wght@500;700&family=Playfair+Display:wght@700&display=swap" rel="stylesheet">
<style>
  :root {
    --page: #e4e4e4;
    --sheet: #ffffff;
    --panel: #f2f2f2;
    --purple: #6b2f9e;
    --blue: #1f64c3;
    --red: #ee4242;
    --navy: #1f1b3d;
    --ink: #1a1a1a;
    --dash: #8a8a8a;
  }
  html, body {
    margin: 0;
    width: 700px;
    height: 1200px;
    overflow: hidden;
    background: var(--page);
  }
  .infographic {
    position: absolute;
    left: 0;
    top: 352px;
    width: 700px;
    height: 495px;
    display: block;
  }
  .brand-name { font-family: "Montserrat", sans-serif; font-weight: 500; font-size: 24px; fill: var(--purple); letter-spacing: 0.5px; }
  .title-number { font-family: "Montserrat", sans-serif; font-weight: 700; font-size: 96px; fill: var(--purple); }
  .title-text { font-family: "Montserrat", sans-serif; font-weight: 700; font-size: 52px; fill: #fff; }
  .skill-heading { font-family: "Playfair Display", serif; font-weight: 700; font-size: 36px; }
  .skill-body { font-family: "Archivo", sans-serif; font-weight: 500; font-size: 15px; fill: var(--ink); }
  .link-label { font-family: "Archivo", sans-serif; font-weight: 700; font-size: 14px; fill: var(--ink); }
  .step-number { font-family: "Playfair Display", serif; font-weight: 700; font-size: 40px; fill: #fff; }
  .site-address { font-family: "Montserrat", sans-serif; font-weight: 500; font-size: 20px; fill: var(--ink); letter-spacing: 2px; }
  .heading-curiosity { fill: var(--purple); }
  .heading-action { fill: var(--blue); }
  .heading-listening { fill: var(--navy); }
  .heading-imagination { fill: var(--red); }
  .panel-mask { fill: var(--panel); }
  .segment { stroke: #fff; stroke-width: 6; stroke-linejoin: round; paint-order: stroke; }
</style>
</head>
<body>
<svg class="infographic" viewBox="0 0 1186 838" xmlns="http://www.w3.org/2000/svg" aria-label="Lumen Circle four key skills cycle">
  <rect class="sheet" width="1186" height="838" fill="var(--sheet)"/>

  <!-- header -->
  <g class="brand-lockup">
    <circle cx="198" cy="76" r="34" fill="var(--purple)"/>
    <text class="brand-name" x="246" y="85">LUMEN CIRCLE</text>
  </g>
  <g class="title">
    <rect x="568" y="42" width="412" height="68" rx="34" fill="var(--purple)"/>
    <text class="title-number" x="514" y="112">4</text>
    <text class="title-text" x="598" y="96">KEY SLKILLS</text>
  </g>

  <rect class="panel" x="34" y="128" width="1118" height="654" fill="var(--panel)"/>

  <!-- dashed cycle path -->
  <ellipse cx="587" cy="443" rx="315" ry="280" fill="none" stroke="var(--dash)" stroke-width="1.3" stroke-dasharray="4 4"/>
  <g class="dash-gaps">
    <rect class="panel-mask" x="460" y="140" width="216" height="60"/>
    <rect class="panel-mask" x="145" y="210" width="275" height="105"/>
    <rect class="panel-mask" x="765" y="205" width="275" height="110"/>
    <rect class="panel-mask" x="170" y="410" width="190" height="42"/>
    <rect class="panel-mask" x="820" y="412" width="140" height="58"/>
    <rect class="panel-mask" x="145" y="570" width="265" height="105"/>
    <rect class="panel-mask" x="765" y="570" width="275" height="105"/>
    <rect class="panel-mask" x="500" y="688" width="170" height="58"/>
  </g>
  <g class="dash-arrows">
    <polygon points="662,165 678,165 672,178" fill="var(--blue)"/>
    <polygon points="294,392 308,392 300,405" fill="var(--purple)"/>
    <polygon points="488,702 500,716 484,716" fill="var(--red)"/>
    <polygon points="858,484 864,498 850,496" fill="var(--blue)"/>
  </g>

  <!-- skill texts -->
  <g class="skill skill-curiosity">
    <text class="skill-heading heading-curiosity" x="150" y="248">Curiosity</text>
    <text class="skill-body" x="150" y="272">Focus on how you can learn from</text>
    <text class="skill-body" x="150" y="290">another’s knowledge and experience</text>
    <text class="skill-body" x="150" y="307">Your curiosity allows you to listen</text>
  </g>
  <g class="skill skill-action" text-anchor="end">
    <text class="skill-heading heading-action" x="1035" y="242">Positive action</text>
    <text class="skill-body" x="1035" y="272">Show your words and actions matter</text>
    <text class="skill-body" x="1035" y="290">Your positive actions lead to curiosity</text>
    <text class="skill-body" x="1035" y="307">about what else is possible</text>
  </g>
  <g class="skill skill-listening">
    <text class="skill-heading heading-listening" x="150" y="605">Listening</text>
    <text class="skill-body" x="150" y="632">Seek to understand before</text>
    <text class="skill-body" x="150" y="650">speaking Your listening allows you</text>
    <text class="skill-body" x="150" y="667">to take in new information</text>
  </g>
  <g class="skill skill-imagination" text-anchor="end">
    <text class="skill-heading heading-imagination" x="1035" y="605">Imagination</text>
    <text class="skill-body" x="1035" y="632">Consider possibilities beyond what</text>
    <text class="skill-body" x="1035" y="650">you know Your imagination can spark</text>
    <text class="skill-body" x="1035" y="667">positive action</text>
  </g>

  <!-- connector labels -->
  <g class="link-labels" text-anchor="middle">
    <text class="link-label" x="568" y="157">Your positive actions</text>
    <text class="link-label" x="568" y="175">will make you curious</text>
    <text class="link-label" x="568" y="192">about what else is possible.</text>
    <text class="link-label" x="264" y="426">Your curiosity will allow</text>
    <text class="link-label" x="264" y="444">you to listen</text>
    <text class="link-label" x="890" y="428">Your imagination</text>
    <text class="link-label" x="890" y="446">identifies positive</text>
    <text class="link-label" x="890" y="464">actions.</text>
    <text class="link-label" x="584" y="705">Your listening will</text>
    <text class="link-label" x="584" y="723">allow you to take in</text>
    <text class="link-label" x="584" y="740">new information</text>
  </g>

  <!-- arrow ring: each segment is one closed band with its arrowhead -->
  <g class="cycle-ring">
    <path class="segment segment-curiosity" fill="var(--purple)"
      d="M607 253.1 A191 191 0 0 0 421.6 347.5 L404.3 337.5 L441.4 422.5 L515.1 401.5 L497.8 391.5 A103 103 0 0 1 597.8 340.6 Z"/>
    <path class="segment segment-listening" fill="var(--navy)"
      d="M397.1 423 A191 191 0 0 0 491.5 608.4 L481.5 625.7 L566.5 588.6 L545.5 514.9 L535.5 532.2 A103 103 0 0 1 484.6 432.2 Z"/>
    <path class="segment segment-imagination" fill="var(--red)"
      d="M567 632.9 A191 191 0 0 0 752.4 538.5 L769.7 548.5 L732.6 463.5 L658.9 484.5 L676.2 494.5 A103 103 0 0 1 576.2 545.4 Z"/>
    <path class="segment segment-action" fill="var(--blue)"
      d="M776.9 463 A191 191 0 0 0 682.5 277.6 L692.5 260.3 L607.5 297.4 L628.5 371.1 L638.5 353.8 A103 103 0 0 1 689.4 453.8 Z"/>
  </g>

  <circle class="ring-hub" cx="587" cy="443" r="54" fill="var(--purple)"/>

  <!-- step numbers -->
  <g class="step-numbers" text-anchor="middle">
    <text class="step-number" x="566" y="312">01</text>
    <text class="step-number" x="442" y="483">02</text>
    <text class="step-number" x="612" y="602">03</text>
    <text class="step-number" x="734" y="432">04</text>
  </g>

  <!-- step icons -->
  <g class="icon icon-bulb" fill="#fff" transform="translate(490 330)">
    <circle cx="0" cy="0" r="12"/>
    <rect x="-6" y="13" width="12" height="7" rx="2"/>
    <rect x="-4" y="22" width="8" height="3"/>
  </g>
  <g class="icon icon-sound" fill="none" stroke="#fff" stroke-width="3" stroke-linecap="round" transform="translate(478 540)">
    <path d="M-14 0 q0 -16 12 -16 q12 0 12 14 q0 9 -9 14 q-5 3 -5 10"/>
    <line x1="16" y1="-12" x2="25" y2="-16"/>
    <line x1="17" y1="-1" x2="26" y2="-1"/>
    <line x1="16" y1="10" x2="25" y2="14"/>
  </g>
  <g class="icon icon-idea" fill="#fff" transform="translate(690 540)">
    <circle cx="0" cy="0" r="13"/>
    <rect x="-6" y="14" width="12" height="7" rx="2"/>
  </g>
  <g class="icon icon-rating" fill="#fff" transform="translate(688 338)">
    <circle cx="-11" cy="-14" r="3.5"/>
    <circle cx="0" cy="-19" r="3.5"/>
    <circle cx="11" cy="-14" r="3.5"/>
    <rect x="-14" y="-2" width="8" height="18"/>
    <rect x="-4" y="-8" width="15" height="24" rx="3"/>
  </g>

  <text class="site-address" x="593" y="811" text-anchor="middle">stylevault.example/lumen-circle</text>
</svg>
</body>
</html>
```